i would like a business card to leave with customers and potential customers for electrical work and for the supply and install of reverse cycle airconditioning in the domestic and commercial market.
I own my own business and im a sole trader. I have an a'class electrical lisence and also a refrigeration lisence so i am
able to offer complete installations in airconditioning by a fully qualified and lisenced tradesman.
im looking for something that comes across as unique and professional.
i had the coluor black and some gold in mind but open to any coluors.
something like Lanterra Electrical & Refrigeration
or Lanterra Air.
i will use this design on a business card to advertise through summer to help generate installs through the busy season.

Target Market(s)

Mainly domestic house holds through summer who are in need of airconditioning and reliable information to acomadate thier cooling and heating requirements

Industry/Entity Type

Electrical

Requirements
Must have
• Business name- Lanterra
My name- Mark Delford
My mobile no- 0438 517 290
My email- mrdelford@qelvo.com.au
Installation & Decomissioning of aiconditioning split systems
LIC NO: TRK 540316
Nice to have
• Lanterra Electrical & Refrigeration

```html
<!DOCTYPE html>
<html lang="en">
<head>
<meta charset="utf-8">
<title>Lanterra Electrical – Business Card</title>
<link rel="stylesheet" href="https://fonts.googleapis.com/css2?family=Crimson+Text&family=Source+Sans+3:wght@300;400&display=swap">
<style>
  :root {
    --backdrop: #2f3a3b;
    --card-top: #2e2e2e;
    --card-bottom: #1c1c1c;
    --ink-light: #e6e6e6;
    --ink-muted: #8a8a8a;
    --ink-name: #a9a9a9;
    --ink-services: #cfcfcf;
    --swoosh-blue: #2a7bc4;
    --badge: #d9d9d9;
  }
  * { margin: 0; padding: 0; box-sizing: border-box; }
  html, body { width: 1200px; height: 900px; overflow: hidden; }
  body { background: var(--backdrop); position: relative; }

  .card {
    position: absolute;
    background: radial-gradient(ellipse at 50% 45%, var(--card-top), var(--card-bottom) 80%);
    overflow: hidden;
  }
  .card--front { left: 111px; top: 133px; width: 436px; height: 714px; }
  .card--back  { left: 662px; top: 135px; width: 435px; height: 711px; }

  .brand-mark {
    position: absolute;
    display: flex;
    align-items: center;
    gap: 16px;
    font-family: "Source Sans 3", sans-serif;
    font-weight: 400;
    color: var(--ink-light);
    font-size: 46px;
    line-height: 1;
  }
  .brand-mark__dot {
    width: 52px; height: 52px; border-radius: 50%;
    background: var(--ink-light);
    flex: none;
  }
  .card--front .brand-mark { left: 50%; top: 357px; transform: translate(-50%, -50%); }
  .card--back .brand-mark { left: 36px; top: 140px; transform: translateY(-50%); }

  .front-title {
    position: absolute; left: 8px; bottom: 10px;
    font-family: "Source Sans 3", sans-serif; font-weight: 300;
    font-size: 43px; letter-spacing: 2.5px; color: var(--ink-light);
    white-space: nowrap;
  }

  .owner-name {
    position: absolute; left: 322px; top: 30px;
    writing-mode: vertical-rl;
    font-family: "Crimson Text", serif;
    font-weight: 400;
    font-size: 50px; letter-spacing: 1px; color: var(--ink-name);
    white-space: nowrap;
  }

  .contact {
    position: absolute; left: 23px; top: 353px;
    list-style: none;
    font-family: "Crimson Text", serif; font-size: 27px; line-height: 34px;
    color: var(--ink-light);
  }
  .contact__label { color: var(--ink-muted); margin-right: 6px; }

  .services {
    position: absolute; left: 17px; top: 525px;
    font-family: "Crimson Text", serif; font-size: 22px; line-height: 27px;
    color: var(--ink-services);
  }

  .swoosh { position: absolute; left: 0; bottom: 0; width: 435px; height: 220px; }

  .authorised-badge {
    position: absolute; left: 362px; top: 635px;
    width: 44px; height: 64px; background: var(--badge);
  }
</style>
</head>
<body>
  <section class="card card--front">
    <div class="brand-mark"><span class="brand-mark__dot"></span>Lanterra</div>
    <p class="front-title">Lanterra Electrical</p>
  </section>

  <section class="card card--back">
    <div class="brand-mark"><span class="brand-mark__dot"></span>Lanterra</div>
    <h1 class="owner-name">Mark Delford</h1>
    <ul class="contact">
      <li><span class="contact__label">mob:</span> 0438 517 290</li>
      <li><span class="contact__label">email:</span>mrdelford@qelvo.com.au</li>
      <li><span class="contact__label">LIC No:</span>TRK 540316</li>
    </ul>
    <p class="services">Installation &amp; Decomissioning of<br>airconditioning Split Systems</p>
    <svg class="swoosh" viewBox="0 0 435 220" aria-hidden="true">
      <defs>
        <linearGradient id="lowerBand" x1="0" y1="0" x2="0" y2="1">
          <stop offset="0" stop-color="#2b2d30"/>
          <stop offset="1" stop-color="#141516"/>
        </linearGradient>
      </defs>
      <path d="M0 150 C170 150 360 110 435 15 L435 220 L0 220 Z" fill="#000"/>
      <path d="M0 140 C170 140 360 100 435 0 L435 18 C360 116 170 156 0 156 Z" fill="var(--swoosh-blue)"/>
      <path d="M0 162 C170 162 362 124 435 34 L435 220 L0 220 Z" fill="url(#lowerBand)"/>
    </svg>
    <div class="authorised-badge"></div>
  </section>
</body>
</html>
```